IT Services Company - Company Logo, Flyer design

We are an IT professional services company that provides technical service and support in the residential market. I would like to create a colorful logo and flyer that will be mainly letterbox dropped.

Target Market(s)

residential

Industry/Entity Type

It Company

Requirements
Must have
• nice look and feel, easy to read

```html
<!DOCTYPE html>
<html lang="en">
<head>
<meta charset="utf-8">
<title>Bayline Communications – IT Services Flyer</title>
<link rel="stylesheet" href="https://fonts.googleapis.com/css2?family=Lato:wght@400;700;900&family=Oswald:wght@600;700&display=swap">
<style>
  :root {
    --orange: #ff5a1f;
    --orange-deep: #f0461a;
    --blue: #2f3fb0;
    --blue-deep: #25319a;
    --ink: #3a3a3a;
    --white: #ffffff;
    --paper: #ffffff;
  }
  * { margin: 0; padding: 0; box-sizing: border-box; }
  html, body { width: 962px; height: 1200px; overflow: hidden; background: var(--paper); }
  .flyer { position: relative; width: 962px; height: 1200px; overflow: hidden; background: var(--paper); font-family: 'Lato', sans-serif; color: var(--ink); }

  .hero-photo {
    position: absolute; left: 0; top: 0; width: 962px; height: 390px;
    background: linear-gradient(100deg, #f4f6fa 0%, #e3e9f1 40%, #dfe6ee 62%, #c9d3df 80%, #eef1f5 100%);
  }

  .brand { position: absolute; left: 52px; top: 48px; display: flex; align-items: center; gap: 16px; }
  .brand-dot { width: 86px; height: 86px; border-radius: 50%; background: var(--blue); }
  .brand-text { display: flex; flex-direction: column; }
  .brand-name { font-family: 'Lato', sans-serif; font-weight: 900; font-size: 50px; line-height: 1; color: var(--blue); letter-spacing: -1px; }
  .brand-sub { font-family: 'Lato', sans-serif; font-weight: 900; font-size: 50px; line-height: 1; color: var(--blue); display: none; }
  .brand-tag { font-family: 'Lato', sans-serif; font-weight: 700; font-size: 13px; letter-spacing: 2.4px; color: #5a5a6a; margin-top: 4px; }

  .banner { position: absolute; left: 0; top: 385px; width: 962px; height: 150px; }
  .banner svg { position: absolute; inset: 0; }
  .banner-text {
    position: absolute; right: 36px; top: 20px; text-align: right;
    font-family: 'Oswald', sans-serif; font-weight: 700; font-size: 31px; line-height: 37px;
    color: var(--white); letter-spacing: 0.2px;
  }

  .services { position: absolute; left: 42px; top: 565px; width: 560px; list-style: none; display: flex; flex-direction: column; gap: 13.5px; }
  .service { display: flex; align-items: flex-start; gap: 18px; font-size: 19.5px; line-height: 22.5px; color: var(--ink); }
  .service svg { flex: 0 0 22px; width: 22px; height: 22px; margin-top: 1px; }

  .offer-panel {
    position: absolute; left: 606px; top: 702px; width: 304px; height: 382px;
    background: linear-gradient(180deg, #3343c4 0%, var(--blue-deep) 100%);
    box-shadow: 0 6px 14px rgba(0,0,0,0.25);
  }
  .offer-band {
    position: absolute; left: 0; top: 116px; width: 304px; height: 94px;
    background: linear-gradient(180deg, #ff6a2c, var(--orange-deep));
    color: var(--white); font-size: 19px; line-height: 24px; text-align: center; padding: 8px 14px 0;
  }
  .offer-note { position: absolute; left: 0; top: 224px; width: 304px; color: var(--white); font-size: 16.5px; line-height: 20px; text-align: center; padding: 0 16px; }

  .rate-badge {
    position: absolute; left: 630px; top: 555px; width: 240px; height: 240px; border-radius: 50%;
    background: var(--white); border: 9px solid var(--orange);
    box-shadow: 0 0 0 7px var(--blue), 0 6px 12px rgba(0,0,0,0.3);
    display: flex; flex-direction: column; align-items: center; justify-content: center; text-align: center;
  }
  .rate-lead { font-weight: 900; font-size: 28px; color: var(--blue); line-height: 1; }
  .rate-price { font-family: 'Oswald', sans-serif; font-weight: 700; font-size: 40px; color: var(--orange-deep); line-height: 1.1; }
  .rate-unit { font-weight: 700; font-size: 24px; color: #111; line-height: 1.1; }
  .rate-cards { font-size: 19px; color: #222; line-height: 22px; margin-top: 4px; }

  .footer { position: absolute; left: 0; top: 1126px; width: 962px; height: 74px; }
  .footer svg { position: absolute; inset: 0; }
  .contact { position: absolute; top: 22px; font-size: 27px; color: var(--white); white-space: nowrap; }
  .contact b { color: var(--orange); font-weight: 700; }
  .contact-phone { left: 46px; }
  .contact-email { left: 372px; }
</style>
</head>
<body>
<main class="flyer">
  <div class="hero-photo" role="img" aria-label="Photo of a smiling support agent wearing a headset in a bright office"></div>

  <header class="brand">
    <div class="brand-dot"></div>
    <div class="brand-text">
      <span class="brand-name">Bayline</span>
      <span class="brand-tag">COMMUNICATIONS PTY LTD</span>
    </div>
  </header>

  <section class="banner">
    <svg width="962" height="150" viewBox="0 0 962 150">
      <polygon points="220,0 962,0 962,150 50,150" fill="#ff5a1f"/>
      <polygon points="220,0 290,0 72,150 50,150" fill="#2f3fb0"/>
    </svg>
    <p class="banner-text">We are an IT professional services company<br>that provides technical service and support for<br>the North Shore residential market</p>
  </section>

  <ul class="services">
    <li class="service"><svg viewBox="0 0 22 22"><circle cx="11" cy="11" r="9" fill="none" stroke="#ff5a1f" stroke-width="1.6"/><path d="M2 11h18M11 2c-4 5-4 13 0 18M11 2c4 5 4 13 0 18" fill="none" stroke="#ff5a1f" stroke-width="1.4"/></svg>Home Network &amp; Wireless setup</li>
    <li class="service"><svg viewBox="0 0 22 22"><circle cx="11" cy="11" r="9" fill="#ff5a1f"/><circle cx="11" cy="11" r="4" fill="#fff"/></svg>Improvements for extending your home Wireless</li>
    <li class="service"><svg viewBox="0 0 22 22"><rect x="2" y="2" width="18" height="18" rx="3" fill="#ff5a1f"/><circle cx="11" cy="12" r="4" fill="none" stroke="#fff" stroke-width="2"/></svg>IP Camera installations – external and internal</li>
    <li class="service"><svg viewBox="0 0 22 22"><path d="M18 9a8 8 0 1 0 0 5" fill="none" stroke="#ff5a1f" stroke-width="2"/><path d="M19 4v6h-6" fill="none" stroke="#ff5a1f" stroke-width="2"/></svg>Backup solutions either at home or to a cloud<br>provider</li>
    <li class="service"><svg viewBox="0 0 22 22"><rect x="4" y="10" width="14" height="10" rx="2" fill="#ff5a1f"/><path d="M7 10V7a4 4 0 0 1 8 0v3" fill="none" stroke="#ff5a1f" stroke-width="2"/></svg>Computer &amp; Network Security</li>
    <li class="service"><svg viewBox="0 0 22 22"><rect x="2" y="5" width="18" height="13" fill="#ff5a1f"/><path d="M2 5l9 7 9-7" fill="none" stroke="#fff" stroke-width="1.6"/></svg>Email setup</li>
    <li class="service"><svg viewBox="0 0 22 22"><circle cx="11" cy="11" r="7" fill="none" stroke="#ff5a1f" stroke-width="3" stroke-dasharray="3 2"/><circle cx="11" cy="11" r="3" fill="#ff5a1f"/></svg>Domain setup and email migration to cloud</li>
    <li class="service"><svg viewBox="0 0 22 22"><path d="M2 9a13 13 0 0 1 18 0M5 12a9 9 0 0 1 12 0M8 15a5 5 0 0 1 6 0" fill="none" stroke="#ff5a1f" stroke-width="2"/><circle cx="11" cy="18" r="1.6" fill="#ff5a1f"/></svg>StreamStick installations and wireless setup –<br>Stream movies and shows to your existing TV</li>
    <li class="service"><svg viewBox="0 0 22 22"><rect x="3" y="3" width="14" height="11" fill="none" stroke="#ff5a1f" stroke-width="2"/><path d="M2 18h16" stroke="#ff5a1f" stroke-width="2"/><circle cx="17" cy="15" r="4" fill="#ff5a1f"/></svg>Computer Setup</li>
    <li class="service"><svg viewBox="0 0 22 22"><rect x="2" y="3" width="18" height="12" fill="none" stroke="#ff5a1f" stroke-width="2"/><path d="M8 19h6M11 15v4" stroke="#ff5a1f" stroke-width="2"/></svg>New computer recommendations</li>
    <li class="service"><svg viewBox="0 0 22 22"><rect x="3" y="3" width="14" height="11" fill="none" stroke="#ff5a1f" stroke-width="2"/><path d="M2 18h16" stroke="#ff5a1f" stroke-width="2"/><rect x="13" y="11" width="8" height="8" fill="#ff5a1f"/></svg>New computer unpacking and setup</li>
    <li class="service"><svg viewBox="0 0 22 22"><rect x="6" y="1" width="10" height="20" rx="2" fill="none" stroke="#ff5a1f" stroke-width="2"/><circle cx="11" cy="17" r="1.2" fill="#ff5a1f"/></svg>Mobile phone setups and training</li>
    <li class="service"><svg viewBox="0 0 22 22"><rect x="4" y="5" width="14" height="10" fill="none" stroke="#ff5a1f" stroke-width="2"/><path d="M1 18h20" stroke="#ff5a1f" stroke-width="2"/></svg>Computer training</li>
    <li class="service"><svg viewBox="0 0 22 22"><rect x="3" y="4" width="6" height="16" rx="1" fill="#ff5a1f"/><rect x="10" y="6" width="9" height="14" fill="none" stroke="#ff5a1f" stroke-width="2"/><path d="M12 10h5M12 13h5M12 16h5" stroke="#ff5a1f" stroke-width="1.4"/></svg>Telephony &amp; Network Cable relations and<br>installations</li>
  </ul>

  <aside class="offer-panel">
    <div class="offer-band">We can procure all new hardware and provide you obligation free quotes.</div>
    <p class="offer-note">No job is too small, please call or email our team who will be happy to assist with your enquiry and schedule an appointment. We can also accommodate afterhours appointments.</p>
  </aside>

  <div class="rate-badge">
    <span class="rate-lead">We charge</span>
    <span class="rate-price">$70 Ex GST</span>
    <span class="rate-unit">per hour</span>
    <span class="rate-cards">(All major credit<br>cards accepted)</span>
  </div>

  <footer class="footer">
    <svg width="962" height="74" viewBox="0 0 962 74">
      <rect x="0" y="0" width="962" height="74" fill="#2f3fb0"/>
      <rect x="0" y="0" width="962" height="6" fill="#ff5a1f"/>
      <polygon points="745,0 962,0 962,74 845,74" fill="#ff5a1f"/>
    </svg>
    <p class="contact contact-phone"><b>Phone :</b> 000 0000 000</p>
    <p class="contact contact-email"><b>Email :</b> LOREM@lorem ipsum</p>
  </footer>
</main>
</body>
</html>
```